Lendquay wedsite and logo refresh

We are looking for someone to refresh the look and feel of Lendquay.co.nz we are moving it towards a more traditional brokerage.

Target Market(s)

30 to 55 year old professionals

Coding

Coded - Design and coding required

Number of Pages Required

3 page

Requirements
Nice to have
• we are needing a modern professional look

```html
<!DOCTYPE html>
<html lang="en">
<head>
<meta charset="utf-8">
<title>Lendquay – Home</title>
<link href="https://fonts.googleapis.com/css2?family=Oswald:wght@400;500;600&family=Montserrat:ital,wght@0,400;0,500;1,400&display=swap" rel="stylesheet">
<style>
:root{
  --brand:#e8441f;
  --brand-dark:#c9371a;
  --ink:#1e1e1e;
  --body:#4a4a4a;
  --muted:#8a8a8a;
  --paper:#ffffff;
  --mist:#e9e7e8;
  --footer:#1f1f1f;
  --line:#cfcfcf;
}
*{box-sizing:border-box;margin:0;padding:0}
html,body{width:1200px;height:3810px;overflow:hidden}
body{position:relative;background:var(--paper);font-family:"Montserrat",sans-serif;color:var(--body)}
.abs{position:absolute}
.display{font-family:"Oswald",sans-serif;text-transform:uppercase;font-weight:500}
.center{left:0;width:1200px;text-align:center}
.eyebrow{font-family:"Oswald",sans-serif;font-size:17px;letter-spacing:1.5px;color:var(--brand);text-transform:uppercase}
.title{font-family:"Oswald",sans-serif;font-weight:500;font-size:40px;color:var(--ink);text-transform:uppercase;line-height:1}
.btn{position:absolute;background:var(--brand);color:#fff;font-family:"Oswald",sans-serif;font-weight:500;text-transform:uppercase;font-size:17px;display:flex;align-items:center;justify-content:center}
.side-label{position:absolute;width:1px;z-index:2}
.side-label i{position:absolute;left:0;width:1px;background:#bdbdbd}
.side-label span{position:absolute;left:-60px;width:120px;text-align:center;transform:rotate(-90deg);font-family:"Oswald",sans-serif;font-size:10px;letter-spacing:1px;color:#666;text-transform:uppercase}

/* header */
.social{position:absolute;width:14px;height:14px;border-radius:50%;background:var(--brand)}
.wordmark{font-family:"Oswald",sans-serif;font-weight:400;color:var(--brand);text-transform:uppercase;letter-spacing:1px}
.login{left:878px;top:28px;font-family:"Oswald",sans-serif;font-size:15px;color:#444;display:flex;align-items:center;gap:5px}
.lang{left:992px;top:18px;display:flex;align-items:center;gap:10px;font-family:"Oswald",sans-serif;font-size:14px;color:#333}
.flag{width:42px;height:42px;border-radius:50%;background:linear-gradient(135deg,#1f3a8a 0%,#c8102e 50%,#1f3a8a 100%)}
.nav{left:111px;top:88px;width:978px;height:76px;background:var(--brand);z-index:10}
.nav a{position:absolute;top:28px;color:#fff;text-decoration:none;font-family:"Oswald",sans-serif;font-size:15px;line-height:18px;text-transform:uppercase;white-space:nowrap}
.nav .active::after{content:"";position:absolute;left:0;right:0;top:29px;height:3px;background:#fff}
.signup{position:absolute;left:763px;top:13px;width:176px;height:46px;background:#fff;color:var(--brand);font-family:"Oswald",sans-serif;font-weight:500;font-size:18px;display:flex;align-items:center;justify-content:center;text-transform:uppercase;white-space:nowrap}

/* hero */
.hero{left:0;top:114px;width:1200px;height:558px;background:linear-gradient(100deg,#6e7a86 0%,#8f8f8c 30%,#a59684 55%,#6b6660 80%,#3f3d3c 100%)}
.hero-headline{left:107px;top:240px;font-size:68px;line-height:73px;color:#fff;z-index:2}

/* services */
.services{left:0;top:1157px;width:1200px;height:686px;background:var(--mist)}
.svc{position:absolute;top:1343px;width:304px;height:328px}
.svc-name{position:absolute;left:0;width:100%;text-align:center;font-family:"Oswald",sans-serif;font-weight:500;font-size:26px;color:#fff;text-transform:uppercase}

/* team */
.team{left:0;top:1843px;width:1200px;height:535px;background:var(--brand)}
.tab{position:absolute;top:2042px;font-family:"Oswald",sans-serif;font-weight:500;font-size:17px;text-transform:uppercase;color:#fff;white-space:nowrap}
.tab em{font-family:"Oswald",sans-serif;font-weight:400;font-size:12px;text-transform:none}
.tab.dim{color:rgba(255,255,255,.35)}

/* mission */
.m-card{position:absolute;top:2645px;width:225px;height:280px;background:#fff;border:1px solid #e2e2e2;box-shadow:0 2px 6px rgba(0,0,0,.08)}
.m-card.featured{background:var(--brand);border-color:var(--brand)}
.m-icon{position:absolute;left:56px;top:-34px;width:112px;height:112px;border-radius:50%;background:#eeeeee;display:flex;align-items:center;justify-content:center}
.featured .m-icon{background:#fff}
.m-title{position:absolute;top:96px;left:0;width:100%;text-align:center;font-family:"Oswald",sans-serif;font-weight:500;font-size:17px;line-height:26px;color:var(--brand);text-transform:uppercase}
.featured .m-title,.featured .m-text{color:#fff}
.m-text{position:absolute;top:161px;left:14px;right:14px;text-align:center;font-size:14px;line-height:26px;color:#666}

/* contact */
.contact-photo{left:580px;top:3020px;width:620px;height:403px;background:linear-gradient(90deg,#f6f4f2 0%,#e8e2dc 35%,#cfc6bd 70%,#b9b2aa 100%)}

/* footer */
.footer{left:0;top:3423px;width:1200px;height:387px;background:var(--footer)}
.f-head{position:absolute;top:3487px;font-family:"Oswald",sans-serif;font-weight:500;font-size:17px;color:#fff;text-transform:uppercase}
.f-list{position:absolute;top:3523px;list-style:none;font-size:16px;line-height:25.7px;color:#fff}
.f-list li::before{content:"»";margin-right:14px}
</style>
</head>
<body>

<!-- hero -->
<section class="abs hero" role="img" aria-label="Photo of business people in a meeting, a bearded man with glasses in the foreground"></section>

<!-- header -->
<header>
  <div class="social" style="left:124px;top:31px"></div>
  <div class="social" style="left:168px;top:31px"></div>
  <div class="social" style="left:212px;top:31px"></div>
  <div class="social" style="left:257px;top:31px"></div>
  <div class="abs wordmark center" style="top:14px;font-size:38px;line-height:1">Lendquay</div>
  <div class="abs login">
    <svg width="15" height="15" viewBox="0 0 16 16"><circle cx="8" cy="8" r="7" fill="none" stroke="#e8441f" stroke-width="1.5"/><circle cx="8" cy="6.5" r="2.3" fill="#e8441f"/><path d="M3.8 12.6c1-2 2.5-2.8 4.2-2.8s3.2.8 4.2 2.8" fill="#e8441f"/></svg>
    LOG IN
  </div>
  <div class="abs lang"><div class="flag" role="img" aria-label="English language flag"></div>ENG ▾</div>
  <nav class="abs nav">
    <a class="active" style="left:82px">Home</a>
    <a style="left:172px">About Us</a>
    <a style="left:288px">Careers</a>
    <a style="left:398px">Media</a>
    <a style="left:490px">Support</a>
    <a style="left:603px">Contact&nbsp; Us</a>
    <div class="signup">Sign&nbsp; Up For Free</div>
  </nav>
</header>

<h1 class="abs display hero-headline">No Obligations<br>No Fees<br>No Worries</h1>
<div class="btn" style="left:109px;top:491px;width:306px;height:55px;font-size:16px;z-index:2">btn-white transform-upper</div>
<div class="side-label" style="left:1159px;top:214px">
  <i style="top:0;height:116px;background:rgba(255,255,255,.6)"></i>
  <span style="top:168px;color:rgba(255,255,255,.8)">Scroll Down</span>
  <i style="top:230px;height:118px;background:rgba(255,255,255,.6)"></i>
</div>

<!-- about -->
<section>
  <div class="side-label" style="left:81px;top:752px">
    <i style="top:0;height:116px"></i><span style="top:168px">About Us</span><i style="top:240px;height:115px"></i>
  </div>
  <div class="abs eyebrow center" style="top:768px">About Us</div>
  <h2 class="abs title center" style="top:800px">Who is Lendquay?</h2>
  <p class="abs" style="left:180px;top:866px;width:840px;text-align:center;font-size:15.5px;line-height:25.8px;color:#555">Lendquay CEO Owen Hartley doesn’t like door knockers. They have a habit of showing up during dinner, or interrupting family time. He decided there must be a better way to field offers,“Our goal is to get major banks, insurance companies, utility companies and other consumer service suppliers fighting for the consumer’s business.”With Lendquay, you can submit a form with a few basic details, and get a range of representative offers back in under 90 seconds.</p>
  <div class="btn" style="left:486px;top:1020px;width:228px;height:50px">Learn More</div>
</section>

<!-- services -->
<section class="abs services"></section>
<div class="side-label" style="left:1136px;top:1323px">
  <i style="top:0;height:116px"></i><span style="top:168px">Services</span><i style="top:240px;height:116px"></i>
</div>
<div class="abs eyebrow center" style="top:1248px">Services</div>
<h2 class="abs title center" style="top:1280px">Find and Compare Rates</h2>

<div class="svc" style="left:123px;background:linear-gradient(160deg,#7b7671 0%,#3d3936 60%,#2a2624 100%)" role="img" aria-label="Photo of hands holding percentage bar symbols">
  <div class="svc-name" style="top:222px">Mortgage Rates</div>
  <svg class="abs" style="left:143px;top:266px" width="18" height="32" viewBox="0 0 18 32"><path d="M9 31V2M2 9l7-7 7 7" fill="none" stroke="#fff" stroke-width="1.5"/></svg>
</div>
<div class="svc" style="left:448px;background:var(--brand)">
  <div class="svc-name" style="top:30px">Personal Finance</div>
  <p class="abs" style="left:36px;top:84px;width:232px;text-align:center;color:#fff;font-size:15px;line-height:26px">Lorem ipsum dolor sit amet, consectetur adipiscing elit, sed do eiusmod tempor incididunt ut labore et dolore magna aliqua Ut enim ad minim veniam.</p>
  <svg class="abs" style="left:143px;top:258px" width="18" height="32" viewBox="0 0 18 32"><path d="M9 1v29M2 23l7 7 7-7" fill="none" stroke="#fff" stroke-width="1.5"/></svg>
</div>
<div class="svc" style="left:773px;background:linear-gradient(150deg,#8c9aa6 0%,#6e6a6d 45%,#8a2a2a 80%,#5a1c1c 100%)" role="img" aria-label="Photo of a family beside a red car with a salesman">
  <div class="svc-name" style="top:222px">Vehicle Finance</div>
  <svg class="abs" style="left:143px;top:266px" width="18" height="32" viewBox="0 0 18 32"><path d="M9 31V2M2 9l7-7 7 7" fill="none" stroke="#fff" stroke-width="1.5"/></svg>
</div>
<div class="btn" style="left:486px;top:1699px;width:228px;height:50px">View All Services</div>

<!-- team -->
<section class="abs team"></section>
<div class="side-label" style="left:59px;top:1933px">
  <i style="top:0;height:116px;background:rgba(255,255,255,.35)"></i><span style="top:168px;color:rgba(255,255,255,.5)">Meet Our Team</span><i style="top:240px;height:116px;background:rgba(255,255,255,.35)"></i>
</div>
<div class="abs eyebrow center" style="top:1934px;color:#fff">Our People</div>
<h2 class="abs title center" style="top:1966px;color:#fff">Meet the Team</h2>
<div class="tab" style="left:222px">Owen Hartley , <em>CEO</em></div>
<div class="tab dim" style="left:499px">Reid Calder , <em>Founder</em></div>
<div class="tab dim" style="left:747px">Tessa Moore , <em>Chief Operations Officer</em></div>
<div class="abs" style="left:155px;top:2085px;width:930px;height:1px;background:rgba(255,255,255,.45)"></div>
<div class="abs" style="left:247px;top:2083px;width:63px;height:5px;border-radius:3px;background:#fff"></div>
<div class="abs" style="left:195px;top:2117px;width:128px;height:128px;border-radius:50%;border:3px solid #fff;background:linear-gradient(180deg,#e9e9e9 0%,#cfcfcf 55%,#1e1e1e 56%,#141414 100%)" role="img" aria-label="Portrait of the CEO in a black branded t-shirt"></div>
<div class="abs" style="left:376px;top:2128px;font-family:'Oswald',sans-serif;font-weight:500;font-size:17px;color:#fff;text-transform:uppercase">Owen Hartley , <em style="font-size:12px;font-weight:400;text-transform:none">CEO</em></div>
<p class="abs" style="left:376px;top:2160px;width:630px;font-style:italic;font-size:14.5px;line-height:26px;color:#fff">Driven to frustration by door to door hawkers, Owen co-founded Lendquay in January 2016, with the aim of putting the power in the hands of the consumer.An innovator by trade, Owen’s prior enterprises include a specialised courier van rental agency, and a building products company, where he designed a revolutionary cladding system, now internationally patented.</p>

<!-- mission -->
<section>
  <div class="side-label" style="left:1136px;top:2532px">
    <i style="top:0;height:116px"></i><span style="top:168px">Our Mission</span><i style="top:240px;height:116px"></i>
  </div>
  <div class="abs eyebrow center" style="top:2469px">Our Mission</div>
  <h2 class="abs title center" style="top:2501px">Why Lendquay?</h2>
  <p class="abs center" style="top:2557px;font-size:17px;color:#444">Our mission is to put the power in the hands of the consumer</p>

  <div class="m-card featured" style="left:121px">
    <div class="m-icon"><svg width="56" height="56" viewBox="0 0 56 56" fill="none" stroke="#e8441f" stroke-width="2"><path d="M28 6l3 6 6.5 1-4.7 4.6 1.1 6.5L28 21l-5.9 3.1 1.1-6.5L18.5 13l6.5-1z"/><path d="M6 38h10l8 4h10a3 3 0 010 6H22m12-6l12-6a3 3 0 013 5l-15 9H16"/></svg></div>
    <div class="m-title">Great Rates &amp;<br>Incentives</div>
    <p class="m-text">Receive the great rates and incentives hassle-free - Lendquay does the shopping around for you.</p>
  </div>
  <div class="m-card" style="left:365px">
    <div class="m-icon"><svg width="56" height="56" viewBox="0 0 56 56" fill="none" stroke="#e8441f" stroke-width="2"><path d="M28 50S14 34 14 22a14 14 0 0128 0c0 12-14 28-14 28z"/><circle cx="28" cy="22" r="6"/><ellipse cx="28" cy="50" rx="14" ry="3"/></svg></div>
    <div class="m-title">Any Time,<br>Any Where</div>
    <p class="m-text">Get notifications and review representative offers wherever you are with your personal.</p>
  </div>
  <div class="m-card" style="left:609px">
    <div class="m-icon"><svg width="56" height="56" viewBox="0 0 56 56" fill="none" stroke="#e8441f" stroke-width="2"><rect x="16" y="6" width="24" height="44" rx="3"/><path d="M24 10h8M26 45h4"/><path d="M12 28c5-6 27-6 32 0-5 6-27 6-32 0z"/><circle cx="28" cy="28" r="4"/></svg></div>
    <div class="m-title">Privacy Is<br>Important</div>
    <p class="m-text">Your private information is disclosed only when you follow up on representative offers from a service.</p>
  </div>
  <div class="m-card" style="left:853px">
    <div class="m-icon"><svg width="56" height="56" viewBox="0 0 56 56" fill="none" stroke="#e8441f" stroke-width="2"><rect x="8" y="26" width="9" height="22"/><path d="M17 28l8-12V8c4 0 6 3 6 7v7h12a3 3 0 013 3l-3 20a3 3 0 01-3 3H17"/><path d="M38 6l2-4M44 10l4-2M42 16l5 1"/></svg></div>
    <div class="m-title">No Fees,<br>No Obligations</div>
    <p class="m-text">Receive the great rates and incentives hassle-free - Lendquay does the shopping around for you.</p>
  </div>
</section>

<!-- contact -->
<section>
  <div class="abs" style="left:0;top:3020px;width:1200px;height:403px;background:#f7f6f5"></div>
  <div class="abs contact-photo" role="img" aria-label="Photo of a smiling woman in a checked shirt using her phone in a bright kitchen"></div>
  <div class="side-label" style="left:59px;top:3040px">
    <i style="top:0;height:116px"></i><span style="top:168px">Get In Touch</span><i style="top:240px;height:116px"></i>
  </div>
  <div class="abs eyebrow" style="left:107px;top:3107px">Contact Us</div>
  <h2 class="abs title" style="left:107px;top:3140px">Get In Touch</h2>
  <p class="abs" style="left:107px;top:3186px;width:490px;font-size:17.5px;line-height:26px;color:#555">Lorem ipsum dolor sit amet, consectetur adipiscing elit, sed do eiusmod tempor incididunt ut labore et dolore magna aliqua.</p>
  <div class="btn" style="left:107px;top:3300px;width:172px;height:50px">Get A Quote</div>
</section>

<!-- footer -->
<footer class="abs footer"></footer>
<div class="abs wordmark" style="left:113px;top:3536px;font-size:42px;line-height:1">Lendquay</div>
<div class="social" style="left:122px;top:3624px;background:#fff"></div>
<div class="social" style="left:169px;top:3624px;background:#fff"></div>
<div class="social" style="left:216px;top:3624px;background:#fff"></div>
<div class="social" style="left:263px;top:3624px;background:#fff"></div>

<div class="f-head" style="left:379px">Quicks Links</div>
<ul class="f-list" style="left:379px"><li>Home</li><li>About Us</li><li>Careers</li><li>Media</li><li>Support</li><li>Contact&nbsp; Us</li></ul>
<div class="f-head" style="left:600px">Our Services</div>
<ul class="f-list" style="left:600px"><li>Mortgage</li><li>Personal Finance</li><li>Vehicle Finance</li><li>Commercial Finance</li><li>Insurance</li><li>Vehicle Leasing</li></ul>
<div class="f-head" style="left:877px">Newsletters</div>
<div class="abs" style="left:877px;top:3528px;width:209px;height:44px;background:#fff;font-size:12px;color:#444;padding:16px 12px">Enter The Email</div>
<div class="btn" style="left:877px;top:3582px;width:209px;height:44px;font-size:18px">Subscribe</div>

<div class="abs" style="left:113px;top:3718px;width:975px;height:1px;background:#3a3a3a"></div>
<div class="abs center" style="top:3736px;font-family:'Oswald',sans-serif;font-size:16px;color:#fff">( C ) Copyrights 2020 <span style="color:var(--brand)">LENDQUAY</span> &nbsp;&nbsp;|&nbsp;&nbsp; All Rights Reserved</div>

</body>
</html>
```